Web design project for exciting Australian start-up

Background
We are looking for a creative and talented web design artist to work alongside our market leading web developer.
• You will be required to create a modern and clean design theme for our website, incorporating selected rustic colour scheme elements for our exciting Australian start-up to operate within the coffee industry.
reoccurring work to be expected to flow to the successful designer.
Requirements
• c. 5 - 10 page website
• Landing page
• Log in/ out
• 404 template
• Typography is emphasised
• Please use either a) typemarrow.com, b) free web fonts, c) brindle fonts
• All design elements in vector format
• Preferably with icons for each header title(i.e. about us, how it works etc) but designer have free reign over how the site looks, so might not be applicable
• All pages to be responsive
• Down to eSlab resolution

High level visual design brief attached - additional pages to be worked from base design.

Design inspiration
• We would like to use design elements from the following sources:
http://www.zandrix.com/halcyon/ (Functionality)
Colour scheme refer to logo and complementary style guide

```html
<!DOCTYPE html>
<html lang="en">
<head>
<meta charset="utf-8">
<title>Brewhaven – Australia's First Online Coffee Marketplace</title>
<link rel="stylesheet" href="https://fonts.googleapis.com/css2?family=Arimo:wght@400;700&family=Titillium+Web:wght@400;600&display=swap">
<style>
  :root {
    --page-bg: #ffffff;
    --rule-grey: #9a9a9a;
    --ink: #111111;
    --charcoal: #4a4b49;
    --charcoal-dark: #3a3b39;
    --btn-dark: #4d4d4d;
    --orange: #f18a21;
    --orange-soft: #e4a35c;
    --orange-deep: #d9701f;
    --footer-text: #f2f2f2;
    --panel-fill: rgba(190, 190, 190, 0.5);
    --panel-edge: #5b5b5b;
    --bean-dark: #3e2417;
    --bean-mid: #5e3722;
    --wood: #7d5237;
  }
  * { box-sizing: border-box; margin: 0; padding: 0; }
  html, body {
    width: 1200px; height: 764px; overflow: hidden;
    background: var(--page-bg);
    font-family: "Arimo", Arial, sans-serif;
    color: var(--ink);
  }
  .canvas { position: relative; width: 1200px; height: 764px; }

  /* Header */
  .header-rule {
    position: absolute; left: 0; width: 1200px; height: 3px;
    background: var(--rule-grey);
  }
  .header-rule.top { top: 48px; }
  .header-rule.bottom { top: 84px; }

  .header-btn {
    position: absolute; top: 55px; height: 25px; z-index: 3;
    display: flex; align-items: center;
    border-radius: 3px; font-size: 10px; text-transform: uppercase;
    color: #fff; text-decoration: none;
  }
  .btn-login { left: 172px; width: 77px; background: var(--btn-dark); font-weight: 700; }
  .btn-login .btn-icon {
    width: 27px; height: 100%; display: flex; align-items: center; justify-content: center;
    border-right: 1px solid #6a6a6a;
  }
  .btn-login .btn-label { padding-left: 11px; }
  .btn-signup { left: 952px; width: 77px; background: var(--orange-soft); }
  .btn-signup .btn-icon { width: 28px; display: flex; justify-content: center; }
  .btn-signup .btn-label { padding-left: 2px; font-size: 11px; }

  .brand {
    position: absolute; top: 22px; left: 0; width: 1200px; height: 90px; z-index: 4;
    display: flex; align-items: center; justify-content: center; gap: 14px;
    pointer-events: none;
  }
  .brand-mark {
    width: 90px; height: 90px; border-radius: 50%;
    background: var(--orange-soft);
    border: 3px solid var(--page-bg);
  }
  .brand-name {
    font-family: "Arimo", Arial, sans-serif; font-weight: 700;
    font-size: 32px; letter-spacing: 3px; color: var(--ink);
    background: var(--page-bg); padding: 0 6px; line-height: 33px;
  }

  /* Hero */
  .hero {
    position: absolute; left: 172px; top: 89px; width: 857px; height: 436px;
    overflow: hidden; z-index: 1;
  }
  .hero-photo {
    position: absolute; inset: 0;
    background: linear-gradient(120deg, #8a6f52 0%, var(--bean-mid) 30%, var(--bean-dark) 60%, var(--wood) 100%);
  }
  .hero-panel {
    position: absolute; left: 48px; top: 66px; width: 302px; height: 318px;
    background: var(--panel-fill);
    border: 2px solid var(--panel-edge);
  }
  .hero-title {
    position: absolute; left: 35px; top: 16px;
    font-family: "Arimo", Arial, sans-serif; font-weight: 400;
    font-size: 43px; line-height: 57px; color: var(--ink);
  }
  .btn-video {
    position: absolute; left: 78px; top: 252px; width: 145px; height: 45px;
    border: 2px solid #6b4a2c; border-radius: 5px;
    background: linear-gradient(#eb9247, var(--orange-deep));
    box-shadow: inset 0 0 0 2px #f4b27a;
    font-family: "Titillium Web", sans-serif; font-size: 17px; color: #fff;
    display: flex; align-items: center; justify-content: center;
    text-transform: uppercase; letter-spacing: 0.3px;
  }
  .hero-edge {
    position: absolute; left: 172px; top: 525px; width: 857px; height: 3px;
    background: var(--orange-soft);
  }

  /* Footer */
  .site-footer {
    position: absolute; left: 172px; top: 528px; width: 857px; height: 167px;
    background: var(--charcoal);
    box-shadow: 0 10px 12px -6px rgba(0,0,0,0.25);
    color: var(--footer-text);
  }
  .footer-col { position: absolute; top: 15px; }
  .footer-col h2 {
    font-family: "Titillium Web", sans-serif; font-weight: 400;
    font-size: 15.5px; color: var(--footer-text);
  }
  .col-help { left: 19px; }
  .col-who { left: 223px; }
  .col-join { left: 413px; }
  .col-news { left: 570px; }
  .col-news h2 { font-family: "Arimo", Arial, sans-serif; font-size: 15px; padding-top: 1px; }
  .footer-links { list-style: none; margin-top: 27px; }
  .footer-links li { font-size: 11px; line-height: 19px; }
  .footer-links a { color: var(--footer-text); text-decoration: none; }

  .news-input {
    position: absolute; left: 570px; top: 69px; width: 266px; height: 30px;
    background: #fff; border: 1px solid #cfcfcf;
    box-shadow: inset 0 2px 3px rgba(0,0,0,0.2);
    font-size: 12px; color: #b5b5b5; padding: 8px 14px;
  }
  .news-btn {
    position: absolute; top: 116px; height: 30px;
    display: flex; align-items: center; gap: 9px; padding-left: 13px;
    font-weight: 700; font-size: 12.5px; color: #fff;
  }
  .btn-subscribe { left: 570px; width: 124px; background: var(--orange); }
  .btn-unsubscribe { left: 712px; width: 124px; background: var(--charcoal-dark); padding-left: 14px; }

  .copyright {
    position: absolute; top: 723px; left: 0; width: 1244px;
    text-align: center; font-size: 11px; color: var(--ink);
  }
</style>
</head>
<body>
<div class="canvas">

  <div class="header-rule top"></div>
  <div class="header-rule bottom"></div>

  <a class="header-btn btn-login" href="#">
    <span class="btn-icon">
      <svg width="9" height="11" viewBox="0 0 9 11"><path d="M2 5V3.5a2.5 2.5 0 0 1 5 0V5" fill="none" stroke="#fff" stroke-width="1.5"/><rect x="0.5" y="5" width="8" height="6" rx="1" fill="#fff"/></svg>
    </span>
    <span class="btn-label">Login</span>
  </a>

  <header class="brand">
    <div class="brand-mark"></div>
    <span class="brand-name">BREWHAVEN</span>
  </header>

  <a class="header-btn btn-signup" href="#">
    <span class="btn-icon">
      <svg width="14" height="14" viewBox="0 0 14 14"><circle cx="6" cy="4" r="3" fill="#2b2b2b"/><path d="M0.5 13.5c0-3.5 2.5-5.5 5.5-5.5s5.5 2 5.5 5.5z" fill="#2b2b2b"/><circle cx="11" cy="11" r="2.6" fill="#fff" stroke="#2b2b2b" stroke-width="1"/></svg>
    </span>
    <span class="btn-label">Sign up</span>
  </a>

  <section class="hero">
    <div class="hero-photo" role="img" aria-label="Photo of a steaming cup of coffee with cinnamon sticks and star anise among roasted coffee beans on a wooden table"></div>
    <div class="hero-panel">
      <h1 class="hero-title">Australia’s<br>First online<br>Coffee<br>Marketplace</h1>
      <a class="btn-video">Watch video</a>
    </div>
  </section>
  <div class="hero-edge"></div>

  <footer class="site-footer">
    <div class="footer-col col-help">
      <h2>Helpful info</h2>
      <ul class="footer-links">
        <li><a href="#">About us</a></li>
        <li><a href="#">Media enquiries</a></li>
        <li><a href="#">Terms &amp; conditions</a></li>
        <li><a href="#">Privacy policy</a></li>
      </ul>
    </div>
    <div class="footer-col col-who">
      <h2>Who we are</h2>
      <ul class="footer-links">
        <li><a href="#">How it works</a></li>
        <li><a href="#">FAQ</a></li>
        <li><a href="#">Contact us</a></li>
      </ul>
    </div>
    <div class="footer-col col-join">
      <h2>Join us on</h2>
      <ul class="footer-links">
        <li><a href="#">Chatterbox</a></li>
        <li><a href="#">Tweetly</a></li>
        <li><a href="#">Linkwell</a></li>
        <li><a href="#">Reelcast</a></li>
      </ul>
    </div>
    <div class="footer-col col-news">
      <h2>Subscribe to our Newsletter</h2>
    </div>
    <div class="news-input">Enter Your Email...</div>
    <div class="news-btn btn-subscribe">
      <svg width="20" height="14" viewBox="0 0 20 14"><rect x="0.5" y="0.5" width="19" height="13" fill="#fff"/><path d="M0.5 0.5L10 8l9.5-7.5M0.5 13.5L7.5 6.5M19.5 13.5l-7-7" fill="none" stroke="#f18a21" stroke-width="1.2"/></svg>
      Subscribe
    </div>
    <div class="news-btn btn-unsubscribe">
      <svg width="20" height="14" viewBox="0 0 20 14"><rect x="0.5" y="0.5" width="19" height="13" fill="#fff"/><path d="M0.5 0.5L10 8l9.5-7.5M0.5 13.5L7.5 6.5M19.5 13.5l-7-7" fill="none" stroke="#3a3b39" stroke-width="1.2"/></svg>
      Unsubscribe
    </div>
  </footer>

  <p class="copyright">Copyright © 2014 Brewhaven</p>

</div>
</body>
</html>
```